K & R Acre Works. Business card design

We need a business card designed for a new business. We have a bulldozer and tractor service. We clear land and make wildlife food plots. We provide disking, bush hogging, and site prep services.
I have attached an image of a business card that I like and would like my business cards to look similar.

Target Market(s)

anyone needing bulldozer and/or tractor services

Industry/Entity Type

Business

Contact Information for Business Card

K & R Acre Works, Operated by 7-T-Ranch
Wade Colton
601-472-3358
wcr4817@fieldmail-example.com

Font styles to use
Sans Serif

Colors

Designer to choose colors to be used in the design.

Requirements
Must have
• image of tractor and bulldozer
• Land Clearing
• Wildlife food plots
• Bush Hogging
• Disking
• Site prep
Nice to have
• i have included a image of a business card that i like. I would like mine to be similar.

```html
<!DOCTYPE html>
<html lang="en">
<head>
<meta charset="utf-8">
<title>K &amp; R Acre Works – Business Card</title>
<link rel="stylesheet" href="https://fonts.googleapis.com/css2?family=Roboto:wght@400;500;700&family=Roboto+Condensed:wght@500;700&display=swap">
<style>
  :root {
    --page-bg: #e4e4e2;
    --card-bg: #f4f4f2;
    --olive: #9b9632;
    --brown: #6e3d12;
    --text: #4a4a4a;
    --rule: #8a8a8a;
    --dozer-tone: #6f7a52;
    --tractor-tone: #8d7a48;
  }
  * { margin: 0; padding: 0; box-sizing: border-box; }
  html, body {
    width: 1200px; height: 771px; overflow: hidden;
    background: var(--page-bg);
    font-family: "Roboto", sans-serif;
  }
  .card {
    position: absolute; left: 300px; top: 213px;
    width: 600px; height: 344px;
    background: var(--card-bg);
    border-radius: 18px;
    overflow: hidden;
    box-shadow: 0 2px 6px rgba(0,0,0,0.12);
  }
  .brand {
    position: absolute; right: 36px; top: 42px;
    text-align: right;
  }
  .brand-name {
    font-family: "Roboto Condensed", sans-serif;
    font-weight: 700; font-size: 24px; letter-spacing: 0.3px;
    color: var(--brown); text-transform: uppercase; line-height: 1;
    display: flex; align-items: center; justify-content: flex-end; gap: 8px;
  }
  .brand-mark { width: 14px; height: 14px; background: var(--olive); }
  .brand-tagline {
    margin-top: 4px;
    font-family: "Roboto Condensed", sans-serif;
    font-weight: 700; font-size: 11.5px; color: #2e2e2e;
    text-transform: uppercase; letter-spacing: 0.1px;
  }
  .photos {
    position: absolute; top: 84px; right: 36px;
    display: flex; gap: 8px;
  }
  .photo { height: 88px; border: 2px solid var(--brown); }
  .photo-dozer { width: 147px; background: linear-gradient(160deg, #5d6b45, var(--dozer-tone) 45%, #b8a23e 70%, #5b4a32); }
  .photo-tractor { width: 118px; background: linear-gradient(160deg, #5e7346, var(--tractor-tone) 55%, #b9562a 75%, #9c8a5a); }
  .person { position: absolute; left: 31px; top: 194px; }
  .person-name {
    font-family: "Roboto Condensed", sans-serif;
    font-weight: 700; font-size: 22px; color: var(--olive);
    text-transform: uppercase; line-height: 1;
  }
  .person-title {
    margin-top: 4px; font-weight: 500; font-size: 14px;
    color: var(--brown); text-transform: uppercase;
  }
  .divider {
    position: absolute; left: 31px; right: 36px; top: 246px;
    height: 1px; background: var(--rule);
  }
  .contact { position: absolute; left: 31px; top: 261px; list-style: none; }
  .contact li {
    display: flex; align-items: center; gap: 7px;
    font-size: 14.5px; color: var(--text); height: 18px;
  }
  .contact svg { width: 13px; height: 13px; fill: var(--olive); }
  .services {
    position: absolute; right: 35px; top: 261px;
    list-style: none; text-align: right;
  }
  .services li { font-size: 14.5px; color: var(--text); height: 18px; }
  .dot {
    display: inline-block; width: 5px; height: 5px; border-radius: 50%;
    background: var(--olive); vertical-align: middle; margin: 0 3px;
  }
  .base-band { position: absolute; left: 0; bottom: 0; width: 600px; height: 7px; }
</style>
</head>
<body>
  <div class="card">
    <div class="brand">
      <div class="brand-name"><span class="brand-mark"></span>K &amp; R Acre Works</div>
      <div class="brand-tagline">For all of your land improvement needs</div>
    </div>

    <div class="photos">
      <div class="photo photo-dozer" role="img" aria-label="Photo of a yellow bulldozer pushing soil on a cleared site"></div>
      <div class="photo photo-tractor" role="img" aria-label="Photo of an orange tractor with front loader in a grassy field"></div>
    </div>

    <div class="person">
      <div class="person-name">Wade Colton</div>
      <div class="person-title">Owner</div>
    </div>

    <div class="divider"></div>

    <ul class="contact">
      <li>
        <svg viewBox="0 0 24 24"><path d="M6.6 10.8a15.1 15.1 0 0 0 6.6 6.6l2.2-2.2a1 1 0 0 1 1-.25 11.4 11.4 0 0 0 3.6.57 1 1 0 0 1 1 1V20a1 1 0 0 1-1 1A17 17 0 0 1 3 4a1 1 0 0 1 1-1h3.5a1 1 0 0 1 1 1c0 1.25.2 2.45.57 3.6a1 1 0 0 1-.25 1z"/></svg>
        601-472-3358
      </li>
      <li>
        <svg viewBox="0 0 24 24"><path d="M2 5h20v14H2z M2 5l10 8 10-8" /><path d="M3 6.5l9 7 9-7V18H3z" fill="#f4f4f2" opacity="0"/></svg>
        wcr4817@fieldmail-example.com
      </li>
      <li>
        <svg viewBox="0 0 24 24"><circle cx="12" cy="12" r="10"/><path d="M6 9c2-1 3 1 5 0s1-3 3-3c1 2 3 3 2 5s-3 1-4 3 1 4-1 5c-2-1-2-3-3-4s-3-1-2-6z" fill="#f4f4f2"/></svg>
        kracreworks-example.com
      </li>
    </ul>

    <ul class="services">
      <li>Land Clearing</li>
      <li>Wildlife food plots<span class="dot"></span>Disking</li>
      <li>Bush Hogging<span class="dot"></span>Site prep</li>
    </ul>

    <svg class="base-band" viewBox="0 0 600 7" preserveAspectRatio="none">
      <polygon points="0,0 391,0 389,7 0,7" fill="#9b9632"/>
      <polygon points="394,0 600,0 600,7 392,7" fill="#6e3d12"/>
    </svg>
  </div>
</body>
</html>
```